Business Card Design - Service Company

Use of the card mainly in living rooms and relations b2b We wish a card with a modern design, blue tones in the background would be a plus The card must be front / back (one side with the logo / the other with the information of contact )

Font styles to use
Serif

Requirements
Must have
• Using the map on the back of the business card Editable format! Photoshop CS2 / Illustrator CS2
Nice to have
• Mivrel Data IT Plein Ouest Commercial Center, 20417 Valmoreto 0491847352 Siret 41873306200018 APE 9511Z https://www.fb.com/boutiquetech.mivreldata www.mivrel-data.com

```html
<!DOCTYPE html>
<html lang="en">
<head>
<meta charset="utf-8">
<title>Mivrel Data IT — Business Card</title>
<link href="https://fonts.googleapis.com/css2?family=Roboto:wght@400;500;700&display=swap" rel="stylesheet">
<style>
  :root {
    --page: #e4e5e7;
    --card-white: #ffffff;
    --card-grey: #6d6e71;
    --brand-blue: #2a87d0;
    --accent-grey: #6b6c70;
    --text-grey: #4a4b4f;
    --white: #ffffff;
  }
  * { margin: 0; padding: 0; box-sizing: border-box; }
  html, body { width: 1200px; height: 900px; overflow: hidden; }
  body {
    background: var(--page);
    font-family: "Roboto", Arial, sans-serif;
    position: relative;
  }
  .card {
    position: absolute;
    left: 260px;
    width: 680px;
    height: 389px;
    overflow: hidden;
    box-shadow: 0 6px 18px rgba(0,0,0,0.18);
  }
  .card--front { top: 41px; background: var(--card-white); }
  .card--back { top: 470px; background: var(--card-grey); }

  .brand {
    position: absolute;
    display: flex;
    align-items: center;
    font-weight: 700;
    letter-spacing: 0.5px;
    white-space: nowrap;
  }
  .brand__mark { display: inline-block; }
  .card--front .brand { top: 58px; right: 70px; font-size: 28px; color: var(--brand-blue); gap: 10px; }
  .card--front .brand__mark { width: 16px; height: 16px; background: var(--brand-blue); }

  .divider {
    position: absolute;
    top: 210px; left: 205px;
    width: 420px; height: 1.5px;
    background: var(--brand-blue);
  }
  .person { position: absolute; left: 62px; top: 166px; }
  .person__name { font-size: 26px; font-weight: 500; color: var(--brand-blue); letter-spacing: 1px; line-height: 32px; }
  .person__role { font-size: 15px; font-weight: 500; color: var(--text-grey); margin-top: 8px; }

  .contacts { position: absolute; left: 62px; top: 250px; list-style: none; }
  .contacts li {
    display: flex; align-items: center; gap: 8px;
    font-size: 16px; font-weight: 500; color: var(--text-grey);
    margin-bottom: 6px;
  }
  .contacts svg { width: 12px; height: 12px; flex: none; }

  .address {
    position: absolute; right: 58px; top: 222px;
    text-align: right; font-size: 16px; font-weight: 500;
    color: var(--text-grey); line-height: 1.5;
  }
  .wave { position: absolute; left: 0; bottom: 0; width: 680px; height: 389px; }

  .card--back .brand {
    top: 150px; left: 0; width: 100%;
    justify-content: center; gap: 16px;
    font-size: 52px; color: var(--white);
  }
  .card--back .brand__mark { width: 26px; height: 26px; background: var(--white); }
  .registration {
    position: absolute; left: 0; width: 100%; bottom: 62px;
    text-align: center; font-size: 19px; font-weight: 500;
    color: var(--white); letter-spacing: 0.5px;
  }
</style>
</head>
<body>

<section class="card card--front" aria-label="Business card, contact side">
  <div class="brand"><span class="brand__mark"></span>Mivrel Data IT</div>
  <div class="divider"></div>
  <div class="person">
    <div class="person__name">AURELIEN COSTA</div>
    <div class="person__role">Director</div>
  </div>
  <ul class="contacts">
    <li>
      <svg viewBox="0 0 12 12"><path d="M3 1 L5 3.5 L4 5 C5 7 6 8 7.5 8.5 L9 7.5 L11 9.5 L9.5 11 C5.5 11 1 6.5 1 2.5 Z" fill="#2a87d0"/></svg>
      0491847352
    </li>
    <li>
      <svg viewBox="0 0 12 12"><circle cx="6" cy="6" r="5" fill="none" stroke="#2a87d0" stroke-width="1.3"/><path d="M1 6 H11 M6 1 C3.5 4 3.5 8 6 11 M6 1 C8.5 4 8.5 8 6 11" fill="none" stroke="#2a87d0" stroke-width="1"/></svg>
      www.mivrel-data.com
    </li>
    <li>
      <svg viewBox="0 0 12 12"><rect x="1" y="1" width="10" height="10" rx="2" fill="#2a87d0"/></svg>
      /boutiquetech.mivreldata
    </li>
  </ul>
  <div class="address">Centre Commercial<br>Plein Ouest, 20417 Valmoreto</div>
  <svg class="wave" viewBox="0 0 680 389" aria-hidden="true">
    <path d="M0 368 L430 340 C445 339 452 336 460 333 L460 338 C452 341 445 344 430 345 L0 373 Z" fill="#6b6c70"/>
    <path d="M0 382 L460 352 C500 348 505 318 545 312 L680 296 L680 389 L0 389 Z" fill="#2a87d0"/>
  </svg>
</section>

<section class="card card--back" aria-label="Business card, brand side">
  <div class="brand"><span class="brand__mark"></span>Mivrel Data IT</div>
  <div class="registration">Siret 41873306200018 APE 9511Z</div>
</section>

</body>
</html>
```